A private security company called "Tavron Security Services Ltd"

Hello everybody,

We need a web page for a company based in NZ. It is mainly an informative website so it would be wonderful if the designer puts their absolute best into making it a website that I would really appreciate. The website needs to show professionalism and also needs to make our web surfers find the information they need in a click. the company's colour is black and silver, and if those two colours could be integrated into the website it would be absolutely lovely. Please do contact me for any information.

Sincerely,
Dorian Vaskel

Industry/Entity Type

Security

```html
<!DOCTYPE html>
<html lang="en">
<head>
<meta charset="utf-8">
<title>Tavron Security Services Ltd</title>
<link href="https://fonts.googleapis.com/css2?family=Oswald:wght@300;400&family=Arimo:wght@400;700&display=swap" rel="stylesheet">
<style>
:root{
  --ink:#1e1e1e;
  --text:#444;
  --muted:#8a8a8a;
  --silver:#d9d9d9;
  --silver-light:#f3f3f3;
  --line:#c9c9c9;
  --hero-top:#4a4a4a;
  --hero-bottom:#262626;
  --footer:#3b3b3b;
  --footer-deep:#333;
  --footer-text:#8d8d8d;
  --input:#5d5d5d;
  --white:#fff;
  --head:"Oswald", "Arial Narrow", sans-serif;
  --body:"Arimo", Arial, sans-serif;
}
*{box-sizing:border-box;margin:0;padding:0}
html,body{width:1200px;height:2623px;overflow:hidden;background:var(--white)}
body{font-family:var(--body);color:var(--text)}
.page{position:relative;width:1200px;height:2623px;overflow:hidden}
.abs{position:absolute}

/* header */
.site-header{position:absolute;left:0;top:0;width:1200px;height:160px;
  background:linear-gradient(#fefefe,#e6e6e6 85%,#d4d4d4);border-bottom:1px solid #bdbdbd}
.brand{position:absolute;left:158px;top:40px;display:flex;align-items:center;gap:12px}
.brand-mark{width:44px;height:44px;border-radius:50%;background:var(--ink)}
.brand-name{font-family:var(--head);font-weight:400;color:var(--ink);line-height:1}
.brand-name .big{display:block;font-size:34px;letter-spacing:3px}
.brand-name .small{display:block;font-size:14px;letter-spacing:.5px;margin-top:4px}
.main-nav{position:absolute;top:99px;left:0;width:1200px;height:20px}
.main-nav a{position:absolute;font-family:var(--body);font-size:13px;color:#333;text-decoration:none;letter-spacing:.2px}
.social{position:absolute;display:flex;gap:9px}
.social span{width:30px;height:30px;border-radius:50%;background:#b5b5b5}

/* hero */
.hero{position:absolute;left:0;top:160px;width:1200px;height:515px;
  background:radial-gradient(ellipse at 45% 35%,#565656,var(--hero-bottom) 75%)}
.hero-visual{position:absolute;left:694px;top:216px;width:262px;height:459px;
  background:linear-gradient(90deg,rgba(255,255,255,0) 0%,rgba(220,220,220,.55) 45%,rgba(160,160,160,.35) 60%,rgba(255,255,255,0) 100%)}
.hero-title{position:absolute;left:218px;top:384px;font-family:var(--head);font-weight:300;
  font-size:33px;line-height:45px;color:#f1f1f1;letter-spacing:.2px}
.hero-title strong{font-weight:400;font-size:38px}
.slide-arrow{position:absolute;width:48px;height:48px;border-radius:50%;background:#6d6d6d}
.slide-arrow svg{position:absolute;left:16px;top:12px}

/* solutions */
.solution{position:absolute;top:726px;width:300px;text-align:center}
.solution-photo{width:186px;height:186px;margin:0 auto;border-radius:50%;
  border:8px solid #e4e4e4;box-shadow:0 0 0 1px #cfcfcf}
.solution h3{font-family:var(--head);font-weight:400;font-size:19px;color:var(--ink);margin-top:17px}
.solution p{font-size:12.5px;line-height:17px;color:#9a9a9a;width:250px;margin:14px auto 0}
.btn{display:inline-block;font-family:var(--body);font-size:12px;color:#333;
  background:linear-gradient(#fff,#dcdcdc);border:1px solid #b9b9b9;border-radius:3px;
  box-shadow:0 1px 2px rgba(0,0,0,.15)}
.solution .btn{width:112px;height:28px;line-height:26px;margin-top:17px}

/* services */
.services{position:absolute;left:0;top:1134px;width:1200px;height:587px;
  background:linear-gradient(#f2f2f2,#e0e0e0);border-top:1px solid #e0e0e0}
.services-title{position:absolute;left:158px;top:1163px;font-family:var(--head);font-size:22px;font-weight:400;color:var(--ink)}
.service-list{position:absolute;left:160px;top:1222px;list-style:none;width:205px}
.service-list li{position:absolute;left:0;font-size:12px;line-height:15px;color:#666;padding-left:30px;width:205px}
.service-list li::before{content:"";position:absolute;left:2px;top:1px;width:13px;height:13px;border-radius:50%;
  background:#fff;border:1px solid #cfcfcf}
.service-list li::after{content:"";position:absolute;left:7px;top:5px;width:4px;height:4px;
  border-top:1px solid #888;border-right:1px solid #888;transform:rotate(45deg)}
.promo{position:absolute;left:158px;top:1431px;width:211px;height:275px;
  background:linear-gradient(90deg,#2e2e2e,#6b6b6b 70%,#8a8a8a)}
.promo-text{position:absolute;left:30px;top:86px;font-family:var(--head);font-weight:300;
  font-size:21px;line-height:30px;color:#fff;letter-spacing:.5px}
.promo-text .call{font-size:17px}
.grid-col{position:absolute;top:1159px;width:223px;height:562px;display:flex;flex-direction:column;
  border-left:1px solid var(--line)}
.grid-col.last{border-right:1px solid var(--line)}
.cell{position:relative;padding:9px 16px 0 16px;background:linear-gradient(#f6f6f6,#e9e9e9)}
.cell + .cell{border-top:1px solid var(--line)}
.cell h4{font-family:var(--head);font-weight:400;font-size:17px;color:var(--ink)}
.cell p{font-size:11.5px;line-height:17px;color:#666;margin-top:17px;letter-spacing:.1px}
.cell p + p{margin-top:14px}
.cell .btn{position:absolute;right:16px;width:70px;height:26px;line-height:24px;font-size:10.5px;text-align:center}

/* industries */
.industries-title{position:absolute;left:0;top:1772px;width:1200px;text-align:center;
  font-family:var(--head);font-weight:400;font-size:38px;color:var(--ink)}
.industry{position:absolute;top:1886px;width:197px;text-align:center}
.industry-photo{width:197px;height:158px;border:5px solid #e9e9e9;box-shadow:0 0 0 1px #d0d0d0}
.industry h5{font-family:var(--head);font-weight:400;font-size:18px;color:var(--ink);margin-top:14px}
.mini-arrow{position:absolute;top:1948px;width:34px;height:34px;border-radius:50%;background:#b9b9b9}
.mini-arrow svg{position:absolute;left:11px;top:9px}

/* footer */
.site-footer{position:absolute;left:0;top:2138px;width:1200px;height:485px;
  background:linear-gradient(#454545,var(--footer) 30%,var(--footer-deep))}
.footer-head{position:absolute;top:2190px;font-family:var(--head);font-weight:300;font-size:28px;color:#f0f0f0}
.about-text{position:absolute;left:158px;top:2268px;width:300px;font-size:11.5px;line-height:16px;color:var(--footer-text)}
.about-text p + p{margin-top:14px}
.quick-links{position:absolute;left:540px;top:2264px;list-style:none}
.quick-links li{font-size:12px;color:var(--footer-text);height:31.5px;padding-left:22px;position:relative;letter-spacing:.3px}
.quick-links li::before{content:"";position:absolute;left:2px;top:4px;width:5px;height:5px;
  border-top:2px solid #dcdcdc;border-right:2px solid #dcdcdc;transform:rotate(45deg)}
.news-intro{position:absolute;left:769px;top:2264px;width:290px;font-size:11.5px;line-height:16px;color:var(--footer-text)}
.field{position:absolute;left:769px;width:275px;height:33px;background:var(--input);
  font-size:12px;color:#ddd;padding:10px 0 0 20px}
.signup{position:absolute;left:769px;top:2432px;width:142px;height:35px;line-height:33px;text-align:center;font-size:12.5px}
.footer-rule{position:absolute;left:0;top:2535px;width:1200px;height:1px;background:#2a2a2a;box-shadow:0 1px 0 #4a4a4a}
.copyright{position:absolute;left:158px;top:2572px;font-size:12px;color:var(--footer-text)}
.site-footer-social span{background:#9a9a9a}
</style>
</head>
<body>
<div class="page">

  <header class="site-header">
    <div class="brand">
      <span class="brand-mark"></span>
      <div class="brand-name"><span class="big">TAVRON</span><span class="small">Security Services Ltd.</span></div>
    </div>
    <div class="social" style="left:934px;top:32px"><span></span><span></span><span></span></div>
    <nav class="main-nav">
      <a style="left:409px">HOME</a>
      <a style="left:478px">OUR SERVICES</a>
      <a style="left:608px">ABOUT</a>
      <a style="left:688px">LOCATIONS</a>
      <a style="left:793px">NEWS</a>
      <a style="left:864px">CAREERS</a>
      <a style="left:960px">CONTACT US</a>
    </nav>
  </header>

  <section class="hero">
    <div class="hero-visual" style="left:534px;top:56px" role="img" aria-label="Security camera mounted on a pole"></div>
    <h1 class="hero-title" style="left:218px;top:224px"><strong>Lorem Ipsum</strong> is simply dummy text of<br>the printing and typesetting industry.</h1>
    <div class="slide-arrow" style="left:104px;top:232px"><svg width="14" height="24" viewBox="0 0 14 24"><path d="M11 2 L3 12 L11 22" fill="none" stroke="#fff" stroke-width="2"/></svg></div>
    <div class="slide-arrow" style="left:1048px;top:232px"><svg width="14" height="24" viewBox="0 0 14 24"><path d="M3 2 L11 12 L3 22" fill="none" stroke="#fff" stroke-width="2"/></svg></div>
  </section>

  <section class="solutions">
    <div class="solution" style="left:124px">
      <div class="solution-photo" role="img" aria-label="Homeowner setting a wall alarm keypad" style="background:linear-gradient(135deg,#c9b8a4,#7d6a5a)"></div>
      <h3>Residential Solutions</h3>
      <p>Lorem ipsum dolor sit amet, consec tetur adipiscing elit. Donec vitae pharetra nunc. Aliquam condimentum neque nibh, ac vestibulum</p>
      <span class="btn">Read More</span>
    </div>
    <div class="solution" style="left:450px">
      <div class="solution-photo" role="img" aria-label="Security guard standing before an office tower" style="background:linear-gradient(135deg,#8fb0cf,#2b3340 65%)"></div>
      <h3>Commercial Solutions</h3>
      <p>Lorem ipsum dolor sit amet, consec tetur adipiscing elit. Donec vitae pharetra nunc. Aliquam condimentum neque nibh, ac vestibulum</p>
      <span class="btn">Read More</span>
    </div>
    <div class="solution" style="left:774px">
      <div class="solution-photo" role="img" aria-label="Operators watching a wall of monitoring screens" style="background:linear-gradient(135deg,#5b86b3,#25384d)"></div>
      <h3>Technology Solutions</h3>
      <p>Lorem ipsum dolor sit amet, consec tetur adipiscing elit. Donec vitae pharetra nunc. Aliquam condimentum neque nibh, ac vestibulum</p>
      <span class="btn">Read More</span>
    </div>
  </section>

  <section class="services"></section>
  <h2 class="services-title">Services</h2>
  <ul class="service-list">
    <li style="top:0">Property guards</li>
    <li style="top:36px">Corporate events security</li>
    <li style="top:73px">Personal bodyguard for high net worth individuals</li>
    <li style="top:128px">Security consultancy</li>
    <li style="top:166px">Private investigation</li>
  </ul>
  <div class="promo" role="img" aria-label="Person at a door with a security keypad">
    <div class="promo-text">CUSTOM<br>OPTIONS<br>AVAILABLE<br><span class="call">CALL 123-456-789</span></div>
  </div>

  <div class="grid-col" style="left:375px">
    <div class="cell" style="height:251px">
      <h4>Property Guards</h4>
      <p>Lorem ipsum dolor sit amet, cons ectetuer adipiscing elit, sed diam nonummy nibh euismod tincidunt</p>
      <p>ut laoreet dolore magna aliquam erat volutpat. Ut wisi enim ad min im veniam, quis nostrud exerci ta tion ullamcorper suscipit lobortis nisl.</p>
      <span class="btn" style="top:212px">Read More</span>
    </div>
    <div class="cell" style="height:311px">
      <h4>Corporate Events Security</h4>
      <p>Lorem ipsum dolor sit amet, cons ectetuer adipiscing elit, sed diam nonummy nibh euismod tincidunt ut laoreet dolore magna aliquam erat volutpat. Ut wisi enim ad mini m veniam, quis nostrud exerci tati on ullamcorper suscipit lobortis n isl ut aliquip ex ea commodo cons equat.</p>
      <span class="btn" style="top:232px">Read More</span>
    </div>
  </div>
  <div class="grid-col" style="left:598px">
    <div class="cell" style="height:270px">
      <h4>Personal Bodyguards</h4>
      <p>Duis autem vel eum iriure dolor i n hendrerit in vulputate velit esse molestie consequat.</p>
      <p>Vel illum dolore eu feugiat nulla f acilisis at vero eros et accumsan et iusto odio dignissim qui bland it praesent luptatum zzril delenit a ugue duis dolore te feugait nulla facilisi.</p>
      <span class="btn" style="top:230px">Read More</span>
    </div>
    <div class="cell" style="height:292px">
      <h4>Security Consultancy</h4>
      <p>Duis autem vel eum iriure dolor in hendrerit in vulputate velit ess e molestie consequat, vel illum d olore eu feugiat nulla facilisis at vero eros et accumsan et iusto o dio dignissim qui blandit praese nt luptatum zzril delenit augue du is dolore</p>
      <span class="btn" style="top:231px">Read More</span>
    </div>
  </div>
  <div class="grid-col last" style="left:821px">
    <div class="cell" style="height:234px">
      <h4>Private Investigation</h4>
      <p>Ut wisi enim ad minim veniam, qu is nostrud exerci tation ullamcorp er suscipit lobortis nisl ut aliquip ex ea commodo consequat. Duis autem vel eum iriure dolor in hen drerit in vulputate velit</p>
      <span class="btn" style="top:194px">Read More</span>
    </div>
    <div class="cell" style="height:328px">
      <h4>Executive Protection</h4>
      <p>Lorem ipsum dolor sit amet, cons ectetuer adipiscing elit, sed diam nonummy nibh euismod tincidunt ut laoreet dolore magna aliquam erat volutpat. Ut wisi enim ad mini m veniam, quis nostrud exerci tati on ullamcorper suscipit lobortis n isl ut aliquip ex ea commodo cons equat.</p>
      <span class="btn" style="top:222px">Read More</span>
    </div>
  </div>

  <h2 class="industries-title">Industries We Serve</h2>
  <div class="mini-arrow" style="left:109px"><svg width="12" height="16" viewBox="0 0 12 16"><path d="M8 2 L3 8 L8 14" fill="none" stroke="#fff" stroke-width="2"/></svg></div>
  <div class="mini-arrow" style="left:1054px"><svg width="12" height="16" viewBox="0 0 12 16"><path d="M4 2 L9 8 L4 14" fill="none" stroke="#fff" stroke-width="2"/></svg></div>
  <div class="industry" style="left:158px">
    <div class="industry-photo" role="img" aria-label="Campus officer talking with students on a lawn" style="background:linear-gradient(#9fb07c,#4f6a3a)"></div>
    <h5>Campus Security</h5>
  </div>
  <div class="industry" style="left:388px">
    <div class="industry-photo" role="img" aria-label="Guard patrolling a shopping centre" style="background:linear-gradient(#b49a7a,#5b4636)"></div>
    <h5>Shoping Center</h5>
  </div>
  <div class="industry" style="left:619px">
    <div class="industry-photo" role="img" aria-label="Security cameras overlooking an industrial harbour" style="background:linear-gradient(#f2f4f6,#b9c3cc)"></div>
    <h5>Industrial Security</h5>
  </div>
  <div class="industry" style="left:848px">
    <div class="industry-photo" role="img" aria-label="Officer watching monitoring screens" style="background:linear-gradient(#6a5346,#2a211c)"></div>
    <h5>Security Monitoring</h5>
  </div>

  <footer class="site-footer"></footer>
  <h3 class="footer-head" style="left:158px">About us</h3>
  <h3 class="footer-head" style="left:540px">Quick Links</h3>
  <h3 class="footer-head" style="left:769px">Newsletter Sigup</h3>
  <div class="about-text">
    <p>Lorem ipsum dolor sit amet, consectetur adipiscing elit. Morbi pellentesque iaculis justo eget fermentum. Pellentesque commodo iaculis neque, vitae tincidun odio pellentesque luctus. Aenean in eros eu magna vestibulum imperdiet pretium nec augue.</p>
    <p>Etiam quis turpis enim. Vestibulum auctor id mauris vulputate consequat. Suspendisse potenti. Cras at imperdiet elit. Integer fringilla tellus non diam condimentum, sed ultricies urna ultricies. Sed cong dui quis dui convallis dictum. Donec malesuada vulputate risus vitae vulputate. Maecenas in congue urna. Sed porttitor bibendum</p>
  </div>
  <ul class="quick-links">
    <li>HOME</li><li>OUR SERVICES</li><li>ABOUT</li><li>LOCATIONS</li><li>NEWS</li><li>CAREERS</li><li>CONTACT US</li>
  </ul>
  <p class="news-intro">Fill the form below and recive our latest offers &amp; updates</p>
  <div class="field" style="top:2332px">Your Name</div>
  <div class="field" style="top:2378px">Your Email</div>
  <span class="btn signup">Signup Now!</span>
  <div class="footer-rule"></div>
  <p class="copyright">Copyright © 2014 Tavron Security Service LTD.</p>
  <div class="social site-footer-social" style="left:934px;top:2563px"><span></span><span></span><span></span></div>

</div>
</body>
</html>
```